Talvique Hotels Business Card and Logo

We need a business card design for a hotel group. I saw a hotel card you designed and really liked it. We have multiple properties with different brands. Were hoping that the card would be unique and find a way to list out all our properties. Our web address is www.talviquehotels.com. I have attached some photos of card designs I like.

Industry/Entity Type

Hotel

Contact Information for Business Card

Scott CurranReneson HotelsChief Operating Officer56 Madera DriveCorte Madera, CA 94925Office 415-891-5013Cell 707-5550143

```html
<!DOCTYPE html>
<html lang="en">
<head>
<meta charset="utf-8">
<title>Talvique Hotels Business Card</title>
<link rel="stylesheet" href="https://fonts.googleapis.com/css2?family=Cinzel:wght@500&family=EB+Garamond:wght@400;600&display=swap">
<style>
  :root {
    --backdrop: #f2f2f2;
    --card-dark: #151515;
    --card-light: #ffffff;
    --gold: #b8892e;
    --ink: #1a1a1a;
    --ink-soft: #3a3a3a;
    --white: #ffffff;
  }
  html, body {
    margin: 0;
    padding: 0;
    width: 1200px;
    height: 757px;
    overflow: hidden;
    background: var(--backdrop);
  }
  .canvas {
    position: relative;
    width: 1200px;
    height: 757px;
    background: var(--backdrop);
  }
  .card {
    position: absolute;
    top: 95px;
    width: 300px;
    height: 499px;
    box-sizing: border-box;
  }
  .card--front {
    left: 190px;
    background: var(--card-dark);
  }
  .card--back {
    left: 683px;
    background: var(--card-light);
  }
  .brand-name {
    position: absolute;
    left: 0;
    right: 0;
    margin: 0;
    text-align: center;
    font-family: "Cinzel", serif;
    font-weight: 500;
    color: var(--gold);
    letter-spacing: 1px;
    white-space: nowrap;
  }
  .card--front .brand-name {
    top: 205px;
    font-size: 23px;
  }
  .card--back .brand-name {
    top: 241px;
    font-size: 21px;
  }
  .website {
    position: absolute;
    left: 0;
    right: 0;
    top: 455px;
    margin: 0;
    text-align: center;
    font-family: "EB Garamond", serif;
    font-weight: 600;
    font-size: 11.5px;
    letter-spacing: 2px;
    color: var(--white);
  }
  .person {
    position: absolute;
    left: 0;
    right: 0;
    top: 76px;
    text-align: center;
    font-family: "EB Garamond", serif;
  }
  .person__name {
    margin: 0;
    font-weight: 600;
    font-size: 16px;
    letter-spacing: 0.5px;
    color: var(--ink);
  }
  .person__title {
    margin: 1px 0 0;
    font-size: 10px;
    color: var(--ink-soft);
  }
  .contact {
    position: absolute;
    left: 0;
    right: 0;
    top: 394px;
    text-align: center;
    font-family: "EB Garamond", serif;
    font-size: 13px;
    color: var(--ink-soft);
  }
  .contact p {
    margin: 0 0 6px;
  }
</style>
</head>
<body>
  <main class="canvas">
    <section class="card card--front" aria-label="Business card front">
      <p class="brand-name">TALVIQUE HOTELS</p>
      <p class="website">www.talviquehotels.com</p>
    </section>

    <section class="card card--back" aria-label="Business card back">
      <div class="person">
        <p class="person__name">BRENT HOLLOWAY</p>
        <p class="person__title">Chief Operating Officer</p>
      </div>
      <p class="brand-name">TALVIQUE HOTELS</p>
      <div class="contact">
        <p class="contact__phones">T: 415-555-0186 | M: 707-5550143</p>
        <p class="contact__address">83 Pellwick Lane Brisdale, CA 94902</p>
      </div>
    </section>
  </main>
</body>
</html>
```